Verlindo Magician

I want the business card for my business to give to people who watch that later I will be employed to show magic here is my website http://www.verlindoillusions.example/I want the interesting design , i am very opened for formal and informal, I watch a lot of design so don't stick to the common shape and form but i hope it can also be produced the thing to write on will be the same as in picture that i will upload , i also will upload the logo for you that so can be easy to useDenis CostilleMagicianMAGICIAN BALSAMO 17 rue des Tilleuls - 25000 BESANÇON contact@verlindoillusions.example tel. 0381 946 157 tel. 0674 219 503

```html
<!DOCTYPE html>
<html lang="fr">
<head>
<meta charset="utf-8">
<title>Verlindo Magician – Business Card</title>
<link href="https://fonts.googleapis.com/css2?family=Didact+Gothic&display=swap" rel="stylesheet">
<style>
  :root {
    --backdrop: #1d1d1f;
    --card: #ffffff;
    --card-shade: #f1f1f3;
    --ink: #141414;
    --ink-soft: #2b2b2b;
    --pattern-a: #f6f2f3;
    --pattern-b: #eeeef1;
    --figure-dark: #1a1a1a;
    --figure-mid: #3a3a3a;
  }
  * { margin: 0; padding: 0; box-sizing: border-box; }
  html, body {
    width: 1200px; height: 895px; overflow: hidden;
    background: var(--backdrop);
    font-family: "Didact Gothic", "Century Gothic", sans-serif;
    color: var(--ink);
  }
  .canvas { position: relative; width: 1200px; height: 895px; }
  .card {
    position: absolute; left: 240px; width: 720px; height: 410px;
    background: var(--card);
    box-shadow: 0 10px 30px rgba(0,0,0,.55);
    overflow: hidden;
  }
  .card--front { top: 22px; }
  .card--back {
    top: 462px;
    background: linear-gradient(160deg, var(--card) 55%, var(--card-shade) 100%);
  }
  .suit-pattern {
    position: absolute; inset: 0;
    background: linear-gradient(135deg, var(--pattern-a), var(--pattern-b));
  }
  .portrait {
    position: absolute;
    background: radial-gradient(ellipse at 50% 35%, var(--figure-mid), var(--figure-dark) 70%);
    border-radius: 46% 46% 12% 12% / 30% 30% 10% 10%;
  }
  .card--front .portrait { left: 285px; top: 70px; width: 160px; height: 185px; }
  .card--back .portrait { left: 475px; top: 45px; width: 155px; height: 180px; }
  .brand-name {
    position: absolute;
    font-size: 40px; letter-spacing: 2px; color: var(--ink);
    display: flex; align-items: center; gap: 10px;
  }
  .brand-name::after {
    content: ""; width: 9px; height: 9px; background: var(--ink);
  }
  .card--front .brand-name { left: 270px; top: 268px; }
  .card--back .brand-name { left: 455px; top: 235px; font-size: 38px; }
  .holder { position: absolute; left: 42px; top: 200px; }
  .holder-name { font-size: 30px; font-weight: 400; letter-spacing: 1px; line-height: 1; }
  .holder-role { font-size: 13px; letter-spacing: 1px; margin-top: 5px; color: var(--ink-soft); }
  .contacts { position: absolute; left: 42px; top: 262px; list-style: none; }
  .contact {
    display: flex; align-items: center; gap: 16px;
    height: 42px; margin-bottom: 4px;
  }
  .contact-icon {
    width: 30px; height: 30px; border-radius: 4px;
    background: var(--ink); display: flex; align-items: center; justify-content: center;
    flex-shrink: 0;
  }
  .contact-icon svg { width: 16px; height: 16px; }
  .contact-text { font-size: 15px; line-height: 1.2; letter-spacing: .3px; white-space: nowrap; }
</style>
</head>
<body>
<main class="canvas">

  <section class="card card--front" aria-label="Card front">
    <div class="suit-pattern" role="img" aria-label="Faint pattern of card suits"></div>
    <div class="portrait" role="img" aria-label="Illustration of the magician holding a playing card"></div>
    <div class="brand-name">VERLINDO</div>
  </section>

  <section class="card card--back" aria-label="Card back">
    <div class="portrait" role="img" aria-label="Illustration of the magician holding a playing card"></div>
    <div class="brand-name">VERLINDO</div>

    <div class="holder">
      <h1 class="holder-name">MARC RAVOULET</h1>
      <p class="holder-role">MAGICIAN</p>
    </div>

    <ul class="contacts">
      <li class="contact">
        <span class="contact-icon">
          <svg viewBox="0 0 24 24" fill="#fff"><path d="M6.6 10.8a15.2 15.2 0 0 0 6.6 6.6l2.2-2.2c.3-.3.7-.4 1-.2 1.1.4 2.3.6 3.6.6.6 0 1 .4 1 1V20c0 .6-.4 1-1 1A17 17 0 0 1 3 4c0-.6.4-1 1-1h3.5c.6 0 1 .4 1 1 0 1.3.2 2.5.6 3.6.1.3 0 .7-.2 1z"/></svg>
        </span>
        <span class="contact-text">0381 946 157<br>0674 219 503</span>
      </li>
      <li class="contact">
        <span class="contact-icon">
          <svg viewBox="0 0 24 24" fill="none" stroke="#fff" stroke-width="1.8"><circle cx="12" cy="12" r="9"/><ellipse cx="12" cy="12" rx="4" ry="9"/><path d="M3 12h18M4.5 7.5h15M4.5 16.5h15"/></svg>
        </span>
        <span class="contact-text">contact@verlindoillusions.example<br>verlindoillusions.example</span>
      </li>
      <li class="contact">
        <span class="contact-icon">
          <svg viewBox="0 0 24 24" fill="#fff"><path d="M12 2a7 7 0 0 0-7 7c0 5.2 7 13 7 13s7-7.8 7-13a7 7 0 0 0-7-7zm0 9.5A2.5 2.5 0 1 1 12 6.5a2.5 2.5 0 0 1 0 5z"/></svg>
        </span>
        <span class="contact-text">17 rue des Tilleuls<br>25120 MONTVAREN</span>
      </li>
    </ul>
  </section>

</main>
</body>
</html>
```